Business Card Design (NEW FILES)

ATTENTION: New vector files are available. Please update your design to reflect/use the new (better resolution) logo images.

Seeking a unique and professional business card design for a commercial drone photography/videography business. The layout should feature
the logo (attached) and include the following information:
Owen Tarrick
614-502-7738
www.skylarkreelworks.example
NRD Certified Remote Pilot

Owen Tarrick

```html
<!DOCTYPE html>
<html lang="en">
<head>
<meta charset="UTF-8">
<title>Skylark Reelworks – Business Card</title>
<link href="https://fonts.googleapis.com/css2?family=Montserrat:wght@400;500;800&display=swap" rel="stylesheet">
<style>
  :root {
    --navy: #1f1d4a;
    --orange: #ec8a4f;
    --card: #ffffff;
    --backdrop: #d3d3d3;
  }
  * { box-sizing: border-box; margin: 0; padding: 0; }
  html, body {
    width: 1200px; height: 900px; overflow: hidden;
    background: var(--backdrop);
    font-family: "Montserrat", sans-serif;
  }
  .sheet {
    width: 1200px; height: 900px;
    display: flex; flex-direction: column; align-items: center; justify-content: center;
    gap: 40px;
  }
  .card {
    position: relative;
    width: 700px; height: 400px;
    background: var(--card);
    border-radius: 34px;
    box-shadow: 0 6px 18px rgba(0,0,0,0.18);
    overflow: hidden;
  }
  .brand {
    display: flex; align-items: center; gap: 14px;
    color: var(--navy);
    font-weight: 500;
    letter-spacing: 0.04em;
    text-transform: uppercase;
    line-height: 1;
    white-space: nowrap;
  }
  .brand-dot {
    flex: none;
    border-radius: 50%;
    background: var(--orange);
  }
  /* Front */
  .card-front .brand {
    position: absolute; left: 0; right: 0; top: 126px;
    justify-content: center;
    font-size: 44px;
  }
  .card-front .brand-dot { width: 32px; height: 32px; }
  .credential-band {
    position: absolute; left: 0; right: 0; top: 318px;
    height: 36px;
    background: var(--orange);
    color: #fff;
    font-size: 17px; font-weight: 500;
    display: flex; align-items: center; justify-content: center;
    letter-spacing: 0.02em;
    white-space: nowrap;
  }
  /* Back */
  .card-back .brand {
    position: absolute; left: 48px; top: 190px;
    font-size: 20px;
    gap: 10px;
  }
  .card-back .brand-dot { width: 16px; height: 16px; }
  .divider {
    position: absolute; left: 350px; top: 112px;
    width: 2px; height: 176px;
    background: var(--orange);
  }
  .contact {
    position: absolute; left: 378px; top: 122px;
    color: var(--navy);
    white-space: nowrap;
  }
  .contact-name {
    color: var(--orange);
    font-weight: 800;
    font-size: 26px;
    letter-spacing: 0.01em;
  }
  .contact-role {
    font-size: 16px;
    margin-top: 2px;
    margin-bottom: 18px;
  }
  .contact-line {
    display: flex; align-items: center; gap: 9px;
    font-size: 15px;
    margin-top: 8px;
  }
  .contact-icon { width: 15px; height: 15px; flex: none; }
</style>
</head>
<body>
<main class="sheet">
  <section class="card card-front">
    <div class="brand"><span class="brand-dot"></span>Skylark Reelworks</div>
    <div class="credential-band">NRD Certified Remote Pilot Fully Insured</div>
  </section>

  <section class="card card-back">
    <div class="brand"><span class="brand-dot"></span>Skylark Reelworks</div>
    <div class="divider"></div>
    <div class="contact">
      <p class="contact-name">Owen Tarrick</p>
      <p class="contact-role">Owner</p>
      <p class="contact-line">
        <svg class="contact-icon" viewBox="0 0 24 24" aria-hidden="true">
          <path fill="var(--orange)" d="M6.6 10.8a15.1 15.1 0 0 0 6.6 6.6l2.2-2.2a1 1 0 0 1 1-.25 11.4 11.4 0 0 0 3.6.57 1 1 0 0 1 1 1V20a1 1 0 0 1-1 1A17 17 0 0 1 3 4a1 1 0 0 1 1-1h3.5a1 1 0 0 1 1 1c0 1.25.2 2.45.57 3.6a1 1 0 0 1-.25 1z"/>
        </svg>
        614-502-7738
      </p>
      <p class="contact-line">
        <svg class="contact-icon" viewBox="0 0 24 24" aria-hidden="true">
          <circle cx="12" cy="12" r="10" fill="none" stroke="var(--orange)" stroke-width="2.4"/>
          <path d="M2 12h20M12 2c3 3.2 3 16.8 0 20M12 2c-3 3.2-3 16.8 0 20" fill="none" stroke="var(--orange)" stroke-width="1.8"/>
        </svg>
        www.skylarkreelworks.example
      </p>
    </div>
  </section>
</main>
</body>
</html>
```